Revamp our wedding venue website

Currently we are using wordpress for our website and hoped to find a designer that can assist us with making the website prettier and more pleasing and draw more interest. www.velmorhall.com is our current site. We are connected to google business mail, so I would prefer to stay with this for now and update our gallery with new photos, blog page and putting the contact us form back on all the pages.

Target Market(s)

20-40 years of age, all ranges of styles and generally clients looking for a different modern feel vs. a hotel hall.

Industry/Entity Type

Wedding

Logo Text

1927 Velmor Hall

Number of Pages Required

4 page

Font styles to use
Serif

Requirements
Must have
• Light, airy feel. Romantic and informative. Mobile friendly and easy to contact us-preferred contact form on all pages. Gallery of photos. Previous reviews
Nice to have
• Bio of staff, maybe some videos, and fun things to do in the area for out of town guests. Maps and also venue blank floor plan.

```html
<!DOCTYPE html>
<html lang="en">
<head>
<meta charset="utf-8">
<title>Blog – 1927 Velmor Hall</title>
<link rel="stylesheet" href="https://fonts.googleapis.com/css2?family=Questrial&family=Crimson+Text:ital,wght@0,600;1,400;1,600&display=swap">
<style>
:root{
  --yellow:#ffe100;
  --yellow-text:#f2cf00;
  --ink:#2f2f2f;
  --grey:#5a5a5a;
  --band:#5e5e5e;
  --white:#ffffff;
  --footer:#222222;
  --footer-base:#151515;
  --panel:#262626;
}
*{box-sizing:border-box;margin:0;padding:0}
html,body{width:1200px;height:2821px;overflow:hidden}
body{position:relative;font-family:"Questrial",sans-serif;color:var(--ink);background:var(--white)}
.abs{position:absolute}

.hero{left:0;top:0;width:1200px;height:626px;
  background:linear-gradient(180deg,#6a6460 0%,#8a6f58 30%,#6b5444 60%,#3e342e 100%)}
.site-header{left:0;top:0;width:1200px;height:86px;background:rgba(60,60,60,.55)}
.wordmark{font-family:"Crimson Text",serif;font-weight:600;font-style:normal;color:var(--white);letter-spacing:.5px}
.brand{left:32px;top:18px;font-size:34px}
.main-nav{right:18px;top:20px;display:flex}
.main-nav a{display:block;color:var(--white);text-decoration:none;font-size:17px;padding:14px 20px;height:49px}
.main-nav a.active{background:var(--yellow)}
.hero-title{left:0;top:270px;width:1200px;text-align:center;color:var(--white);font-size:50px;font-weight:700;letter-spacing:-1px}
.hero-sub{left:0;top:336px;width:1200px;text-align:center;color:var(--white);font-size:19px}

.tagline-band{left:0;top:626px;width:1200px;height:90px;background:var(--band);
  border-top:3px dashed var(--yellow);border-bottom:3px dashed var(--yellow)}
.tagline-band p{font-family:"Crimson Text",serif;font-style:italic;font-weight:600;color:var(--yellow);font-size:32px;text-align:center;line-height:84px}

.backdrop{left:0;top:716px;width:1200px;height:1682px;
  background:linear-gradient(160deg,#f4f2ee 0%,#e7e4df 35%,#f6f4f1 60%,#ece3d8 78%,#f8f7f5 100%)}

.post{left:11px;width:775px;height:405px;background:var(--white)}
.post h2{position:absolute;left:0;top:18px;width:100%;text-align:center;font-size:34px;font-weight:400;color:var(--yellow-text)}
.post .thumb{position:absolute;left:30px;top:85px;width:210px;height:164px;
  background:linear-gradient(180deg,#9fc4dc 0%,#cfdde5 45%,#eef0f0 70%,#b9a99a 100%)}
.post .excerpt{position:absolute;left:250px;top:64px;font-size:19.5px;line-height:25.5px;color:var(--ink);white-space:nowrap}
.post .excerpt span{display:block}
.post .more{position:absolute;left:250px;top:280px;font-size:25px;color:var(--yellow-text);text-decoration:none}
.post .meta{position:absolute;left:136px;top:330px;display:flex;align-items:center;gap:36px}
.post .byline{font-size:25px;color:var(--yellow-text)}

.comments{left:809px;width:370px;height:405px;background:var(--white)}
.comments h3{position:absolute;left:26px;top:18px;font-size:26px;font-weight:400;color:var(--ink)}
.comment{position:absolute;left:20px;width:330px}
.comment .avatar{position:absolute;left:0;top:0;width:42px;height:42px;border-radius:50%;background:#3d3d3d}
.comment .name{position:absolute;left:48px;top:0;font-size:19px;color:var(--yellow-text)}
.comment .date{position:absolute;left:48px;top:24px;font-size:10.5px;color:var(--ink);white-space:nowrap}
.comment .body{position:absolute;left:10px;top:48px;width:300px;font-size:10.5px;line-height:14px;color:var(--yellow-text)}
.comment-field{position:absolute;left:25px;top:291px;width:331px;height:47px;border:2px solid var(--grey);font-size:14px;color:#888;padding:12px 10px}
.reply{position:absolute;left:248px;top:344px;width:108px;height:36px;background:var(--grey);color:var(--white);font-size:20px;text-align:center;line-height:36px}

.enquire{left:830px;top:2009px;width:352px;height:361px;background:var(--panel);border:3px solid #d9c51a}
.enquire h4{position:absolute;left:41px;top:35px;width:274px;height:41px;background:var(--yellow);color:var(--white);font-size:29px;font-weight:400;text-align:center;line-height:41px}
.enquire .row{position:absolute;left:0;width:340px;height:41px}
.enquire label{position:absolute;right:248px;top:9px;color:var(--white);font-size:18px}
.enquire .field{position:absolute;left:100px;top:0;width:230px;height:41px;background:var(--white);font-size:17px;padding:10px 12px;color:var(--ink)}
.quote{position:absolute;left:108px;top:276px;width:170px;height:52px;background:var(--white);border:4px solid var(--yellow);border-radius:26px;text-align:center;line-height:44px;font-size:18px}

.comment-band{left:0;top:2398px;width:1200px;height:113px;background:var(--yellow)}
.comment-band .input{position:absolute;left:213px;top:30px;width:526px;height:58px;background:var(--white)}
.comment-band .button{position:absolute;left:754px;top:30px;width:192px;height:55px;background:var(--grey);color:var(--white);font-size:28px;text-align:center;line-height:55px}

.site-footer{left:0;top:2511px;width:1200px;height:245px;background:var(--footer)}
.site-footer .brand-foot{position:absolute;left:0;top:56px;width:100%;text-align:center;font-size:36px}
.foot-nav{position:absolute;left:0;top:150px;width:100%;display:flex;justify-content:center;gap:32px}
.foot-nav a{color:var(--white);font-size:36px;text-decoration:none}
.foot-nav a.active{color:var(--yellow)}
.footer-base{left:0;top:2756px;width:1200px;height:65px;background:var(--footer-base)}
</style>
</head>
<body>

<div class="abs hero" role="img" aria-label="Photo of a bride and groom embracing in front of the brick venue entrance"></div>
<header class="abs site-header">
  <div class="abs brand wordmark">1927 Velmor Hall</div>
  <nav class="abs main-nav">
    <a href="#">Home</a><a href="#">Weddings</a><a href="#">Events</a><a href="#" class="active">Blog</a><a href="#">Gallery</a><a href="#">Contact Us</a>
  </nav>
</header>
<h1 class="abs hero-title">WELCOME TO OUR BLOG</h1>
<p class="abs hero-sub">very informative articles for your wedding plans</p>

<div class="abs tagline-band"><p>Imagine your wedding or event in Tampa’s premiere, unique and historic venue</p></div>

<div class="abs backdrop" role="img" aria-label="Soft photo of two gold wedding rings on white fabric"></div>

<svg width="0" height="0" style="position:absolute"><defs><polygon id="star" points="18,1 22.5,12.5 35,13 25,21 28.5,34 18,26.5 7.5,34 11,21 1,13 13.5,12.5" fill="#f5c518" stroke="#c9960c" stroke-width="1"/></defs></svg>

<article class="abs post" style="top:743px">
  <h2>How to choose the best wedding locstion</h2>
  <div class="thumb" role="img" aria-label="Photo of a reception set by the water"></div>
  <p class="excerpt"><span>When choosing the location for your wedding or</span><span>event, the 1927 Velmor Hall provides you with an</span><span>all-inclusive experience, from the moment you</span><span>arrive, through the creativguests a front-row seat to</span><span>our creative, and talented chefs, as they prepare a</span><span>culinary experience like no other. The full, and spa-</span><span>cious bar, serves up wonderful libations and special-</span><span>ty cocktails that enhance your experience.</span></p>
  <a class="more" href="#">Read more</a>
  <div class="meta">
    <svg width="190" height="36" viewBox="0 0 190 36" aria-label="Five stars"><use href="#star"/><use href="#star" x="38"/><use href="#star" x="76"/><use href="#star" x="114"/><use href="#star" x="152"/></svg>
    <span class="byline">Posted By Tobias</span>
  </div>
</article>
<aside class="abs comments" style="top:743px">
  <h3>Top comments</h3>
  <div class="comment" style="top:51px"><div class="avatar" role="img" aria-label="Commenter avatar"></div><span class="name">Marek Dovan</span><span class="date">commented on Fri 30th October 2015</span><p class="body">When choosing the location for your wedding or event, the Velmor Hall provides you with an all-inclusive experience, from the moment you arrive, through the creative food, and</p></div>
  <div class="comment" style="top:170px"><div class="avatar" role="img" aria-label="Commenter avatar"></div><span class="name">Marek Dovan</span><span class="date">commented on Fri 30th October 2015</span><p class="body">When choosing the location for your wedding or event, the Velmor Hall provides you with an all-inclusive experience, from the moment you arrive, through the creative food, and</p></div>
  <div class="comment-field">type comment here</div>
  <div class="reply">Reply</div>
</aside>

<article class="abs post" style="top:1166px">
  <h2>How to choose the best wedding locstion</h2>
  <div class="thumb" role="img" aria-label="Photo of a reception set by the water"></div>
  <p class="excerpt"><span>When choosing the location for your wedding or</span><span>event, the 1927 Velmor Hall provides you with an</span><span>all-inclusive experience, from the moment you</span><span>arrive, through the creativguests a front-row seat to</span><span>our creative, and talented chefs, as they prepare a</span><span>culinary experience like no other. The full, and spa-</span><span>cious bar, serves up wonderful libations and special-</span><span>ty cocktails that enhance your experience.</span></p>
  <a class="more" href="#">Read more</a>
  <div class="meta">
    <svg width="190" height="36" viewBox="0 0 190 36" aria-label="Five stars"><use href="#star"/><use href="#star" x="38"/><use href="#star" x="76"/><use href="#star" x="114"/><use href="#star" x="152"/></svg>
    <span class="byline">Posted By Tobias</span>
  </div>
</article>
<aside class="abs comments" style="top:1166px">
  <h3>Top comments</h3>
  <div class="comment" style="top:51px"><div class="avatar" role="img" aria-label="Commenter avatar"></div><span class="name">Marek Dovan</span><span class="date">commented on Fri 30th October 2015</span><p class="body">When choosing the location for your wedding or event, the Velmor Hall provides you with an all-inclusive experience, from the moment you arrive, through the creative food, and</p></div>
  <div class="comment" style="top:170px"><div class="avatar" role="img" aria-label="Commenter avatar"></div><span class="name">Marek Dovan</span><span class="date">commented on Fri 30th October 2015</span><p class="body">When choosing the location for your wedding or event, the Velmor Hall provides you with an all-inclusive experience, from the moment you arrive, through the creative food, and</p></div>
  <div class="comment-field">type comment here</div>
  <div class="reply">Reply</div>
</aside>

<article class="abs post" style="top:1584px">
  <h2>How to choose the best wedding locstion</h2>
  <div class="thumb" role="img" aria-label="Photo of a reception set by the water"></div>
  <p class="excerpt"><span>When choosing the location for your wedding or</span><span>event, the 1927 Velmor Hall provides you with an</span><span>all-inclusive experience, from the moment you</span><span>arrive, through the creativguests a front-row seat to</span><span>our creative, and talented chefs, as they prepare a</span><span>culinary experience like no other. The full, and spa-</span><span>cious bar, serves up wonderful libations and special-</span><span>ty cocktails that enhance your experience.</span></p>
  <a class="more" href="#">Read more</a>
  <div class="meta">
    <svg width="190" height="36" viewBox="0 0 190 36" aria-label="Five stars"><use href="#star"/><use href="#star" x="38"/><use href="#star" x="76"/><use href="#star" x="114"/><use href="#star" x="152"/></svg>
    <span class="byline">Posted By Tobias</span>
  </div>
</article>
<aside class="abs comments" style="top:1584px">
  <h3>Top comments</h3>
  <div class="comment" style="top:51px"><div class="avatar" role="img" aria-label="Commenter avatar"></div><span class="name">Marek Dovan</span><span class="date">commented on Fri 30th October 2015</span><p class="body">When choosing the location for your wedding or event, the Velmor Hall provides you with an all-inclusive experience, from the moment you arrive, through the creative food, and</p></div>
  <div class="comment" style="top:170px"><div class="avatar" role="img" aria-label="Commenter avatar"></div><span class="name">Marek Dovan</span><span class="date">commented on Fri 30th October 2015</span><p class="body">When choosing the location for your wedding or event, the Velmor Hall provides you with an all-inclusive experience, from the moment you arrive, through the creative food, and</p></div>
  <div class="comment-field">type comment here</div>
  <div class="reply">Reply</div>
</aside>

<form class="abs enquire">
  <h4>ENQUIRE</h4>
  <div class="row" style="top:96px"><label>Name</label><div class="field">nora fenwick</div></div>
  <div class="row" style="top:143px"><label>Email</label><div class="field">hello@mailbox.net</div></div>
  <div class="row" style="top:190px"><label>Date</label><div class="field">12-20-2015</div></div>
  <div class="row" style="top:237px"><label>Type</label><div class="field">wedding or event</div></div>
  <div class="quote">Get Quote</div>
</form>

<section class="abs comment-band">
  <div class="input"></div>
  <div class="button">Comment</div>
</section>

<footer class="abs site-footer">
  <div class="brand-foot wordmark">1927 Velmor Hall</div>
  <nav class="foot-nav"><a href="#">Home</a><a href="#">Weddings</a><a href="#">Events</a><a href="#" class="active">Blog</a><a href="#">Gallery</a><a href="#">Contact Us</a></nav>
</footer>
<div class="abs footer-base"></div>

</body>
</html>
```